BUSINESS CARD DESIGN

NAME- DALE VORSKIN
PHONE NUMER - 555- 714-9082
EMAIL- OFFICE@TRV-GROUNDMAKRZ.COM
BACK OF CARD- SPEACIALIZES IN LAND CLEARING, FORESTRY MUCLHING AND EXCAVATION

Contact Information for Business Card

NAME- DALE VORSKIN PHONE NUMER - 555- 714-9082 EMAIL- OFFICE@TRV-GROUNDMAKRZ.COM BACK OF CARD- SPEACIALIZES IN LAND CLEARING , MUCLHING AND EXCAVATION

```html
<!DOCTYPE html>
<html lang="en">
<head>
<meta charset="utf-8">
<title>Traverse Groundmakrz LLC – Business Card</title>
<link href="https://fonts.googleapis.com/css2?family=Roboto:wght@300;400;700&display=swap" rel="stylesheet">
<style>
  :root {
    --backdrop: #e3e7e9;
    --card: #1f1f22;
    --pattern-light: #2a2a2d;
    --pattern-dark: #18181a;
    --accent: #f5ac19;
    --text-light: #f2f2f2;
  }
  * { margin: 0; padding: 0; box-sizing: border-box; }
  html, body {
    width: 1200px;
    height: 960px;
    overflow: hidden;
    background: var(--backdrop);
    font-family: "Roboto", sans-serif;
  }
  .card {
    position: absolute;
    left: 250px;
    width: 701px;
    height: 400px;
    background: var(--card);
    border-bottom: 2px solid var(--accent);
    overflow: hidden;
  }
  .card--front { top: 60px; }
  .card--back { top: 500px; }

  .pattern-field {
    position: absolute;
    inset: 0;
    background: radial-gradient(circle at 50% 40%, var(--pattern-light), var(--pattern-dark));
  }

  .brand {
    position: absolute;
    left: 0;
    right: 0;
    top: 118px;
    text-align: center;
    color: var(--accent);
    font-weight: 700;
  }
  .brand__dot {
    display: block;
    width: 70px;
    height: 70px;
    margin: 0 auto 18px;
    border-radius: 50%;
    background: var(--accent);
  }
  .brand__name {
    font-size: 19px;
    letter-spacing: 2px;
    line-height: 1.3;
  }
  .brand__phone {
    margin-top: 8px;
    font-size: 11px;
    letter-spacing: 7px;
  }

  .tagline {
    position: absolute;
    left: 0;
    right: 0;
    top: 357px;
    text-align: center;
    color: var(--text-light);
    font-size: 15px;
    font-weight: 400;
    letter-spacing: 0.6px;
  }

  .person {
    position: absolute;
    left: 0;
    right: 0;
    top: 152px;
    text-align: center;
    color: var(--accent);
    font-size: 44px;
    letter-spacing: 1px;
    line-height: 1;
  }
  .person__first { font-weight: 700; }
  .person__last { font-weight: 300; }

  .contact {
    position: absolute;
    left: 0;
    right: 0;
    top: 248px;
    text-align: center;
    color: var(--text-light);
    font-size: 15px;
    font-weight: 400;
    letter-spacing: 1px;
    line-height: 23px;
    list-style: none;
  }
</style>
</head>
<body>
  <section class="card card--front">
    <div class="pattern-field" role="img" aria-label="Faint repeating company emblem pattern across the dark card"></div>
    <div class="brand">
      <span class="brand__dot"></span>
      <p class="brand__name">TRAVERSE GROUNDMAKRZ LLC</p>
      <p class="brand__phone">555-714-9082</p>
    </div>
    <p class="tagline">SPEACIALIZES IN LAND CLEARING , MUCLHING AND EXCAVATION</p>
  </section>

  <section class="card card--back">
    <h1 class="person"><span class="person__first">DALE</span> <span class="person__last">VORSKIN</span></h1>
    <ul class="contact">
      <li>555- 714-9082</li>
      <li>WWW.TRV-GROUNDMAKRZ.COM</li>
      <li>OFFICE@TRV-GROUNDMAKRZ.COM</li>
    </ul>
  </section>
</body>
</html>
```